American cannabis tech company business card design

Pavrel.com is seeking a modern, professional, and brand-aligned business card that represents our company and its core values: Mission, Story, Values, and Impact. As an innovative cannabis company, we want a business card that is not only visually appealing but also serves as a representation of who we are and what we stand for.

Project Scope: Design a double-sided business card that integrates our brand identity and core values. Incorporate our key brand elements, ensuring a sleek and contemporary aesthetic. Visually reflect our core values (Mission, Story, Values, Impact) in a way that is engaging yet professional.

Target Market(s)

Vendors, third parties,

Contact Information for Business Card

Contact details (name, title, email, phone, website, etc.)

Font styles to use
Other font styles liked:
• Caslon, Centra

Colors

Designer to choose colors to be used in the design.

Requirements
Must have
• Pavrel.com logo and branding A creative yet clean way to integrate our core values (Mission, Story, Values, Impact) Modern typography and a well-structured layout
Nice to have
• forest green, grey, white, black
Should not have
• references to marijuana, leafs, plants, or related product

```html
<!DOCTYPE html>
<html lang="en">
<head>
<meta charset="UTF-8">
<title>Pavrel Business Card</title>
<link rel="stylesheet" href="https://fonts.googleapis.com/css2?family=Poppins:wght@400;600;700&display=swap">
<style>
  :root {
    --forest: #163218;
    --ink: #222822;
    --paper: #ffffff;
    --backdrop: #9b9b9b;
    --rule: #b5b5b5;
  }
  * { margin: 0; padding: 0; box-sizing: border-box; }
  html, body {
    width: 1093px; height: 1200px; overflow: hidden;
    background: var(--backdrop);
    font-family: "Poppins", sans-serif;
  }
  .canvas { position: relative; width: 1093px; height: 1200px; }
  .card {
    position: absolute; left: 265px; width: 578px; height: 356px;
    border-radius: 22px; overflow: hidden;
  }
  .card--front { top: 226px; background: var(--paper); }
  .card--back { top: 621px; background: var(--forest); }
  .front__band {
    position: absolute; left: 0; right: 0; bottom: 0; height: 12px;
    background: var(--forest);
  }
  .front__brand {
    position: absolute; left: 40px; top: 150px; width: 222px;
    font-weight: 700; font-size: 50px; line-height: 56px; letter-spacing: 1px;
    color: var(--forest); text-align: center;
  }
  .front__divider {
    position: absolute; left: 289px; top: 74px; width: 1px; height: 209px;
    background: var(--rule);
  }
  .front__person { position: absolute; left: 314px; top: 98px; }
  .person__name {
    font-weight: 600; font-size: 22px; line-height: 26px; color: var(--forest);
    letter-spacing: 0.2px;
  }
  .person__title { font-size: 16.5px; line-height: 18px; color: var(--ink); }
  .front__contacts { position: absolute; left: 312px; top: 176px; list-style: none; }
  .contact {
    display: flex; align-items: center; height: 26px; font-size: 17px;
    color: var(--ink);
  }
  .contact__icon { width: 24px; height: 24px; margin-right: 3px; flex: none; }
  .back__brand {
    position: absolute; left: 0; right: 0; top: 126px;
    font-weight: 700; font-size: 92px; line-height: 100px; letter-spacing: 2px;
    color: var(--paper); text-align: center;
  }
</style>
</head>
<body>
<main class="canvas">
  <section class="card card--front">
    <div class="front__brand">PAVREL</div>
    <div class="front__divider"></div>
    <div class="front__person">
      <p class="person__name">DANIEL HARPER</p>
      <p class="person__title">Managing Director</p>
    </div>
    <ul class="front__contacts">
      <li class="contact">
        <svg class="contact__icon" viewBox="0 0 24 24" aria-hidden="true">
          <circle cx="12" cy="12" r="12" fill="#163218"/>
          <path d="M8 6.5l2 2.3-1 1.4c.8 1.8 2.1 3.1 3.8 3.9l1.4-1 2.3 2-1.3 1.7c-4.2-.6-7.9-4.3-8.5-8.5z" fill="#fff"/>
          <path d="M13 6.5a4.5 4.5 0 0 1 4.5 4.5M13 8.6a2.4 2.4 0 0 1 2.4 2.4" stroke="#fff" stroke-width="1.1" fill="none"/>
        </svg>
        <span>071-482 390 615</span>
      </li>
      <li class="contact">
        <svg class="contact__icon" viewBox="0 0 24 24" aria-hidden="true">
          <circle cx="12" cy="12" r="12" fill="#163218"/>
          <rect x="5.5" y="8" width="13" height="9" fill="#fff"/>
          <path d="M5.5 8l6.5 5 6.5-5M5.5 17l4.6-4.3M18.5 17l-4.6-4.3" stroke="#163218" stroke-width="0.9" fill="none"/>
        </svg>
        <span>hello@pavrel.com</span>
      </li>
      <li class="contact">
        <svg class="contact__icon" viewBox="0 0 24 24" aria-hidden="true">
          <circle cx="12" cy="12" r="12" fill="#163218"/>
          <g stroke="#fff" stroke-width="1" fill="none">
            <circle cx="12" cy="12" r="6"/>
            <ellipse cx="12" cy="12" rx="2.6" ry="6"/>
            <path d="M6 12h12M7 9h10M7 15h10"/>
          </g>
        </svg>
        <span>www.pavrel-tech.com</span>
      </li>
    </ul>
    <div class="front__band"></div>
  </section>

  <section class="card card--back">
    <div class="back__brand">PAVREL</div>
  </section>
</main>
</body>
</html>
```